Letter and Envelope Design For Harborline Realty

Please design a letter and an envelope incorporating our logo (See Attached). We are also launched a business card contest. Since we want them to match, please feel free to submit a design for both the business card and also the letter design and envelope.

Requirements
Must have
• The envelope, the letter and the business cards must match somehow connecting the designs. We want them to have something that holds them together besides the logo.

```html
<!DOCTYPE html>
<html lang="en">
<head>
<meta charset="utf-8">
<title>Harborline Realty – Letter and Envelope</title>
<link rel="stylesheet" href="https://fonts.googleapis.com/css2?family=Montserrat:wght@500&family=Work+Sans:wght@400;500&display=swap">
<style>
:root{
  --navy:#283080;
  --ink:#4a4a4a;
  --grey:#575757;
  --rule:#3b4583;
  --stage:#ebebeb;
  --paper:#ffffff;
}
*{margin:0;padding:0;box-sizing:border-box}
html,body{width:1200px;height:762px;overflow:hidden;background:var(--stage)}
body{position:relative;font-family:"Work Sans",Arial,sans-serif;color:var(--ink)}
.sheet{position:absolute;background:var(--paper);box-shadow:0 3px 8px rgba(0,0,0,.18);overflow:hidden}
.letter{left:45px;top:52px;width:466px;height:658px}
.envelope-front{left:549px;top:52px;width:606px;height:302px}
.envelope-back{left:549px;top:408px;width:606px;height:302px;background:var(--navy)}

.brand{position:absolute;text-align:center;font-family:"Montserrat",Arial,sans-serif;font-weight:500;color:var(--navy)}
.brand-dot{display:block;margin:0 auto;border:2.5px solid var(--navy);border-radius:50%}
.brand-name{display:block;letter-spacing:.14em;line-height:1.1;white-space:nowrap}
.brand-sub{display:block;letter-spacing:.3em;line-height:1.1}

.letter .brand{left:0;width:466px;top:24px}
.letter .brand-dot{width:60px;height:60px}
.letter .brand-name{font-size:16px;margin-top:8px}
.letter .brand-sub{font-size:12px;margin-top:2px}

.salutation{position:absolute;left:33px;top:178px;font-size:13.5px;color:var(--navy)}
.body-copy{position:absolute;left:33px;top:206px;width:403px}
.body-copy p{font-size:9.2px;line-height:12.1px;margin-bottom:15px;color:#555}
.closing{position:absolute;left:33px;top:495px;font-size:10.5px;color:#444}
.signature{position:absolute;left:33px;top:516px;width:84px;height:12px;background:linear-gradient(90deg,#c9c9c9,#e4e4e4);border-radius:2px}

.rule{position:absolute;height:1px;background:var(--rule)}
.letter .rule{left:33px;width:402px;top:578px}
.contacts{position:absolute;list-style:none;color:#444}
.contacts li{display:flex;align-items:center;gap:4px;white-space:nowrap}
.contacts svg{flex:none}
.contacts strong{color:var(--navy);font-weight:500}
.address{position:absolute;text-align:right;color:#444}
.letter .contacts{left:33px;top:597px;font-size:8px}
.letter .contacts li{height:11px}
.letter .address{right:32px;top:597px;font-size:8px;line-height:11px}
.swoosh{position:absolute;left:0;bottom:0;display:block}

.envelope-front .brand{left:24px;top:22px;width:180px}
.envelope-front .brand-dot{width:54px;height:54px}
.envelope-front .brand-name{font-size:15px;margin-top:7px}
.envelope-front .brand-sub{font-size:11px;margin-top:1px}
.envelope-front .rule{left:24px;width:558px;top:207px}
.envelope-front .contacts{left:24px;top:225px;font-size:10px}
.envelope-front .contacts li{height:13.5px}
.envelope-front .address{right:24px;top:225px;font-size:10px;line-height:13.5px}

.flap{position:absolute;left:0;top:0;display:block}
.watermark{position:absolute;left:276px;top:19px;width:54px;height:54px;border:2px solid rgba(255,255,255,.08);border-radius:50%}
.envelope-back .brand{left:0;width:606px;top:151px;color:#fff}
.envelope-back .brand-dot{width:62px;height:62px;border-color:#fff}
.envelope-back .brand-name{font-size:18px;margin-top:8px}
.envelope-back .brand-sub{font-size:13px;margin-top:2px}
</style>
</head>
<body>

<section class="sheet letter" aria-label="Letterhead">
  <div class="brand">
    <span class="brand-dot"></span>
    <span class="brand-name">HARBORLINE</span>
    <span class="brand-sub">REALTY</span>
  </div>

  <h1 class="salutation" style="font-weight:400">Dear Sir</h1>
  <div class="body-copy">
    <p>Lorem ipsum dolor sit amet, an vel recteque dissentiet, detracto albucius platonem ex vel, eros repudiandae cu. Atqui aliquando nec an, unum graece adolescens vel ad. Id odio scae has, iudico euismod atomorum ius ea, cum ea honestatis quaerendum theophrastus. Mea honestatis quaerendum theophrastus. Mea</p>
    <p>Lorem ipsum dolor sit amet, an vel recteque dissentiet, detracto albucius platonem ex vel, eros repudiandae cu. Atqui aliquando nec an, unum graece adolescens vel ad. Id odio scae has, iudico euismod atomorum ius ea, cum ea honestatis quaerendum theophrastus. Mea doming repudiandae ex, cu cum civibus assentior posidonium. Quo etiam pertinax ex, te eros repudiandae cu. Atqui aliquando nec an, unum graece adolescens vel ad. Id odio scae honestatis quaerendum theophrastus. Mea</p>
    <p>Lorem ipsum dolor sit amet, an vel recteque dissentiet, detracto albucius platonem ex vel, eros repudiandae cu. Atqui aliquando nec an, unum graece adolescens vel ad. Id odio scae has, iudico euismod atomorum ius ea, cum ea honestatis quaerendum theophrastus. Mea honestatis quaerendum theophrastus. Mea</p>
    <p>Lorem ipsum dolor sit amet, an vel recteque dissentiet, detracto albucius platonem ex vel, eros repudiandae cu. Atqui aliquando nec an, unum graece adolescens vel ad. Id odio scae has, iudico euismod atomorum ius ea, cum ea honestatis quaerendum theophrastus. Mea honestatis quaerendum theophrastus. Mea</p>
  </div>
  <p class="closing">Kind Regards</p>
  <div class="signature" role="img" aria-label="Handwritten signature of the sender"></div>

  <div class="rule"></div>
  <ul class="contacts">
    <li><svg width="5" height="6" viewBox="0 0 10 12"><path d="M2 1l2 0 1 3-1.5 1a6 6 0 0 0 3 4L8 8l2 1v2c-5 1-10-5-8-10z" fill="var(--navy)"/></svg>(555) 013-4471</li>
    <li><svg width="6" height="5" viewBox="0 0 12 9"><rect x=".5" y=".5" width="11" height="8" fill="none" stroke="var(--navy)"/><path d="M.5.5l5.5 5 5.5-5" fill="none" stroke="var(--navy)"/></svg>info@harborline.co</li>
    <li><svg width="6" height="6" viewBox="0 0 12 12"><circle cx="6" cy="6" r="5.5" fill="var(--navy)" opacity=".7"/></svg>www.<strong>harborline</strong>.co</li>
  </ul>
  <p class="address">42b Quay Lane,<br>Lyttelton, NZ, 8082</p>
  <svg class="swoosh" width="466" height="40" viewBox="0 0 466 40">
    <path d="M101 40C180 20 270 8 345 4 L320 4C240 8 160 20 101 40z" fill="var(--grey)"/>
    <path d="M140 40C220 18 310 4 380 2C420 2 450 4 466 6V40z" fill="var(--navy)"/>
  </svg>
</section>

<section class="sheet envelope-front" aria-label="Envelope front">
  <div class="brand">
    <span class="brand-dot"></span>
    <span class="brand-name">HARBORLINE</span>
    <span class="brand-sub">REALTY</span>
  </div>
  <div class="rule"></div>
  <ul class="contacts">
    <li><svg width="6" height="7" viewBox="0 0 10 12"><path d="M2 1l2 0 1 3-1.5 1a6 6 0 0 0 3 4L8 8l2 1v2c-5 1-10-5-8-10z" fill="var(--navy)"/></svg>(555) 013-4471</li>
    <li><svg width="7" height="5" viewBox="0 0 12 9"><rect x=".5" y=".5" width="11" height="8" fill="none" stroke="var(--navy)"/><path d="M.5.5l5.5 5 5.5-5" fill="none" stroke="var(--navy)"/></svg>info@harborline.co</li>
    <li><svg width="7" height="7" viewBox="0 0 12 12"><circle cx="6" cy="6" r="5.5" fill="var(--navy)" opacity=".7"/></svg>www.<strong>harborline</strong>.co</li>
  </ul>
  <p class="address">42b Quay Lane,<br>Lyttelton, NZ, 8082</p>
  <svg class="swoosh" width="606" height="36" viewBox="0 0 606 36">
    <path d="M162 36C260 14 380 4 466 0L440 0C350 4 240 14 162 36z" fill="var(--grey)"/>
    <path d="M200 36C300 12 420 0 500 0C550 0 590 2 606 4V36z" fill="var(--navy)"/>
  </svg>
</section>

<section class="sheet envelope-back" aria-label="Envelope back">
  <svg class="flap" width="606" height="100" viewBox="0 0 606 100">
    <path d="M10 0C14 40 10 94 58 96H548C596 94 592 40 596 0" fill="var(--navy)" stroke="rgba(0,0,0,.25)" stroke-width="1.5"/>
    <path d="M12 4C16 42 14 97 58 99H548C592 97 590 42 594 4" fill="none" stroke="rgba(0,0,0,.08)" stroke-width="3"/>
  </svg>
  <div class="watermark"></div>
  <div class="brand">
    <span class="brand-dot"></span>
    <span class="brand-name">HARBORLINE</span>
    <span class="brand-sub">REALTY</span>
  </div>
</section>

</body>
</html>
```